Blockchain Analytics Firm Needs Logo And Website Design

We need a logo and a very basic website for a company based in Linköping, Sweden called 'Vextor'. We build custom machine learning and AI solutions for companies based on blockchain. We are not picky about the colors, but the design should communicate modernity and stability.
We like the following websites:
https://www.pallidwren.co.uk/
https://www.tormacapitalhouse.com/
Target Market(s)
Our customers are startups that have their own product based on blockchain or other distributed ledger technology.
Industry/Entity Type
It Company
Contact Information for Business Card
Name, title and email address
Logo Text
Our company name and "Blockchain Analytics"
Font styles to use
Colors
Designer to choose colors to be used in the design.
Requirements
Must have
- The website and logo need to be modern and clean. In the beginning, we will not be filling out all sections of the website (team, clients, etc.) but we will need to have these set up so we can eventually use them.
Nice to have
- We like angular graphics and some animations on the webpage would be nice.

```html
<!DOCTYPE html>
<html lang="en">
<head>
<meta charset="utf-8">
<title>Vextor — Blockchain Analytics</title>
<link href="https://fonts.googleapis.com/css2?family=Poppins:wght@400;500;600&family=Roboto:wght@500;700&display=swap" rel="stylesheet">
<style>
:root{
  --ink:#111827;
  --text:#2b2b2b;
  --muted:#555;
  --red:#ee4037;
  --purple:#5b2ee0;
  --blue:#3b9be8;
  --orange:#f39322;
  --navy:#0b1636;
  --teal-bg:#d9eaea;
  --rule:#3a8fc4;
  --white:#fff;
}
*{box-sizing:border-box;margin:0;padding:0}
html,body{width:1200px;height:3209px;overflow:hidden}
body{position:relative;background:var(--white);font-family:"Poppins",sans-serif;color:var(--text)}
.abs{position:absolute}
/* header */
.hero-art{left:0;top:0}
.brand{left:110px;top:30px;display:flex;align-items:center;gap:12px}
.brand-mark{width:34px;height:34px;background:var(--red)}
.brand-name{font-family:"Poppins",sans-serif;font-weight:500;font-size:26px;color:var(--red);line-height:1}
.brand-sub{font-size:17px;color:var(--red);font-weight:500}
.nav{left:428px;top:50px;display:flex;align-items:center;gap:26px}
.nav a{color:var(--white);text-decoration:none;font-size:14px;font-weight:500;letter-spacing:.3px}
.nav .login{border:2px solid var(--white);border-radius:20px;padding:4px 24px;margin-left:18px}
.hero-title{left:110px;top:240px;font-family:"Roboto",sans-serif;color:var(--ink)}
.hero-title h1{font-size:42px;font-weight:700;line-height:1.1}
.hero-title h2{font-size:33px;font-weight:500;line-height:1.2}
.hero-copy{left:110px;top:348px;width:430px;font-size:12.5px;line-height:23px;color:var(--text)}
.btn{display:inline-block;border-radius:20px;font-size:13px;font-weight:600;padding:9px 22px;text-transform:uppercase;letter-spacing:.3px}
.btn-outline{border:2px solid var(--purple);color:var(--purple)}
.btn-red{background:var(--red);color:var(--white);border:2px solid var(--red)}
.hero-btns{left:110px;top:452px;display:flex;gap:18px}
.dots{left:112px;top:518px;display:flex;gap:8px;align-items:center}
.dots span{width:10px;height:10px;border-radius:50%;background:var(--ink)}
.dots .on{width:14px;height:14px;background:var(--white);border:3px solid var(--ink)}
/* welcome */
.video{left:135px;top:700px;width:465px;height:330px;border:5px solid #e4e4e4;box-shadow:0 4px 12px rgba(0,0,0,.25);background:linear-gradient(135deg,#222 0%,#3a2f50 50%,#1a1a2a 100%)}
.play{left:328px;top:845px;width:70px;height:70px;border-radius:50%;background:rgba(20,20,20,.7);border:3px solid var(--white)}
.play::after{content:"";position:absolute;left:26px;top:20px;border-left:22px solid var(--white);border-top:13px solid transparent;border-bottom:13px solid transparent}
.welcome-title{left:648px;top:726px;font-family:"Roboto",sans-serif;font-size:31px;font-weight:700;color:var(--ink)}
.welcome-copy{left:648px;top:788px;width:450px;font-size:12.5px;line-height:28px}
.welcome-btn{left:648px;top:964px}
/* services */
.services{left:0;top:1130px;width:1200px;height:763px;background:linear-gradient(180deg,#fafafa,#f2f2f2)}
.section-title{width:1200px;left:0;text-align:center;font-family:"Roboto",sans-serif;font-weight:700;color:var(--ink);font-size:36px}
.services-copy{left:160px;top:1257px;width:880px;text-align:center;font-size:12.5px;line-height:30px}
.service-card-hl{left:436px;top:1385px;width:321px;height:385px;background:var(--white);box-shadow:0 3px 14px rgba(0,0,0,.18)}
.service{top:1410px;width:300px;text-align:center}
.service svg{display:block;margin:0 auto}
.service h3{font-weight:500;font-size:18px;color:var(--ink);margin-top:26px}
.service p{font-size:12px;line-height:24px;margin-top:14px}
/* blog */
.blog{left:0;top:1893px;width:1200px;height:870px;background:var(--teal-bg)}
.blog-rule{left:566px;top:2066px;width:68px;height:3px;background:var(--rule)}
.post{width:293px;height:382px;background:var(--white);border-radius:6px;box-shadow:0 2px 8px rgba(0,0,0,.18);overflow:hidden}
.post-img{height:185px}
.post-body{padding:20px 18px}
.post-date{font-size:14px;color:var(--ink);display:flex;gap:8px;align-items:center}
.post h4{font-size:13px;font-weight:600;color:#1e2a66;line-height:23px;margin-top:10px;text-transform:uppercase}
.post p{font-size:12px;line-height:21px;margin-top:10px}
.clouds{left:0;top:2640px}
/* footer */
.foot h5{font-size:17px;font-weight:600;color:var(--ink);letter-spacing:.3px}
.foot-text{font-size:11px;line-height:19px;margin-top:26px;width:285px}
.email-field{margin-top:20px;width:278px;height:40px;border:1px solid #ccc;font-size:11px;padding:12px 14px;color:var(--muted)}
.sub-btn{margin-top:22px;display:inline-block;background:var(--red);color:var(--white);font-size:13px;font-weight:600;padding:10px 30px}
.contact-list{margin-top:26px;list-style:none;font-size:12px;line-height:18px}
.contact-list li{display:flex;gap:14px;margin-bottom:12px}
.links{margin-top:26px;list-style:none;font-size:11px;line-height:22px}
.links li::before{content:"▸";margin-right:10px;font-size:9px}
.social{margin-top:24px;list-style:none;font-size:13px}
.social li{display:flex;align-items:center;gap:10px;margin-bottom:10px}
.social li span{width:22px;height:22px;border:1.5px solid var(--ink);border-radius:50%}
.foot-rule{left:0;top:3095px;width:1200px;height:1px;background:#e2e2e2}
.copyright{left:0;width:1200px;top:3140px;text-align:center;font-size:12px}
</style>
</head>
<body>

<svg class="abs hero-art" width="1200" height="580" viewBox="0 0 1200 580" aria-hidden="true">
  <defs>
    <linearGradient id="heroFill" x1="0" y1="0" x2="1" y2="1">
      <stop offset="0" stop-color="#0a1a4a"/>
      <stop offset=".5" stop-color="#1d2f8a"/>
      <stop offset="1" stop-color="#071030"/>
    </linearGradient>
  </defs>
  <path d="M380 0 L1200 0 L1200 420 Q1200 440 1180 455 L960 560 Q925 575 900 548 L390 35 Q372 16 380 0Z" fill="var(--purple)"/>
  <path d="M400 0 L1200 0 L1200 405 L955 540 Q930 552 912 532 L408 22 Z" fill="url(#heroFill)" role="img" aria-label="Glowing blue chain links over a dark digital background"/>
</svg>

<div class="abs brand">
  <div class="brand-mark"></div>
  <div><div class="brand-name">VEXTOR</div><div class="brand-sub">Blockchain Analytics</div></div>
</div>

<nav class="abs nav">
  <a href="#">HOME</a><a href="#">ABOUT</a><a href="#">OUR SERVICES</a><a href="#">ANALYTICS</a><a href="#">BLOG</a><a href="#">CONTACT</a><a href="#" class="login">LOGIN</a>
</nav>

<div class="abs hero-title"><h1>VEXTOR</h1><h2>BLOCKCHAIN ANALYTICS</h2></div>
<p class="abs hero-copy">Sed ut perspiciatis unde omnis iste natus error sit voluptatem accusantium doloremque laudantium, totam rem aperiam, eaque ipsa quae ab illo inventore veritatis et quasi architecto beatae</p>
<div class="abs hero-btns"><span class="btn btn-outline">Set up demo</span><span class="btn btn-red">Watch demo</span></div>
<div class="abs dots"><span class="on"></span><span></span><span></span><span></span></div>

<div class="abs video" role="img" aria-label="Video still of two presenters on a stage in front of a projected screen"></div>
<div class="abs play"></div>
<h2 class="abs welcome-title">WELCOME TO VEXTOR</h2>
<p class="abs welcome-copy">Sed ut perspiciatis unde omnis iste natus error sit voluptatem accusantium doloremque laudantium, totam rem aperiam, eaque ipsa quae ab illo litore veritatis et quasi architecto beatae vitae dicta sunt explicabo. Nemo enim ipsam voluptatem quia voluptas sit aspernatur aut odit aut fugit, sed quia ntur magni dolores eos qui ratione voluptatem sequi nesciunt.</p>
<span class="abs btn btn-red welcome-btn">Read more</span>

<div class="abs services"></div>
<h2 class="abs section-title" style="top:1186px">OUR SERVICES</h2>
<p class="abs services-copy">Sed ut perspiciatis unde omnis iste natus error sit voluptatem accusantium doloremque laudantium, totam rem aperiam, eaque ipsa quae ab illo inventore veritatis et quasi architecto beatae vitae dicta sunt explicabo.</p>
<div class="abs service-card-hl"></div>

<div class="abs service" style="left:120px">
  <svg width="130" height="130" viewBox="0 0 130 130" aria-hidden="true"><rect x="24" y="78" width="30" height="30" fill="var(--orange)" transform="rotate(45 39 93)"/><rect x="35" y="15" width="82" height="82" rx="6" fill="var(--red)" transform="rotate(45 76 56)"/><circle cx="76" cy="56" r="17" fill="none" stroke="#fff" stroke-width="2"/><circle cx="76" cy="56" r="5" fill="#fff"/></svg>
  <h3>Blockchain Analytics</h3>
  <p>Sed ut perspiciatis unde omnis iste natus error sit voluptatem accusantium doloremque laudantium, totam rem aperiam, eaque ipsa quae ab illo inventore veritatis et quasi architecto beatae vitae dicta</p>
</div>
<div class="abs service" style="left:447px">
  <svg width="130" height="130" viewBox="0 0 130 130" aria-hidden="true"><rect x="24" y="78" width="30" height="30" fill="var(--orange)" transform="rotate(45 39 93)"/><rect x="35" y="15" width="82" height="82" rx="6" fill="var(--purple)" transform="rotate(45 76 56)"/><rect x="64" y="46" width="24" height="16" fill="none" stroke="#fff" stroke-width="2"/><path d="M60 66 H92" stroke="#fff" stroke-width="2"/></svg>
  <h3>AI solutions</h3>
  <p>Sed ut perspiciatis unde omnis iste natus error sit voluptatem accusantium doloremque laudantium, totam rem aperiam, eaque ipsa quae ab illo inventore veritatis et quasi architecto beatae vitae dicta</p>
</div>
<div class="abs service" style="left:790px">
  <svg width="130" height="130" viewBox="0 0 130 130" aria-hidden="true"><rect x="24" y="78" width="30" height="30" fill="var(--orange)" transform="rotate(45 39 93)"/><rect x="35" y="15" width="82" height="82" rx="6" fill="var(--blue)" transform="rotate(45 76 56)"/><circle cx="76" cy="50" r="8" fill="none" stroke="#fff" stroke-width="2"/><path d="M64 68 H88 M70 60 L82 60" stroke="#fff" stroke-width="2"/></svg>
  <h3>Custom Machine Learning</h3>
  <p>Sed ut perspiciatis unde omnis iste natus error sit voluptatem accusantium doloremque laudantium, totam rem aperiam, eaque ipsa quae ab illo inventore veritatis et quasi architecto beatae vitae dicta</p>
</div>

<div class="abs blog"></div>
<h2 class="abs section-title" style="top:1990px">LATEST BLOG</h2>
<div class="abs blog-rule"></div>

<article class="abs post" style="left:132px;top:2178px">
  <div class="post-img" role="img" aria-label="People in an office overlaid with network icons" style="background:linear-gradient(135deg,#5a7fb0,#c9d8ea 60%,#7e8fa8)"></div>
  <div class="post-body"><div class="post-date">▦ October 17, 2018</div><h4>Quis autem vel eum iure reprehen derit qui in ea voluptate</h4><p>Sed ut perspiciatis unde omnis iste natus error sit voluptatem accusantium doloremque latium, totam rem aperiam</p></div>
</article>
<article class="abs post" style="left:455px;top:2138px">
  <div class="post-img" role="img" aria-label="Two colleagues reviewing a document in a server room" style="background:linear-gradient(135deg,#1b3d7a,#5d4a52 55%,#2a5aa0)"></div>
  <div class="post-body"><div class="post-date">▦ October 17, 2018</div><h4>Quis autem vel eum iure reprehen derit qui in ea voluptate</h4><p>Sed ut perspiciatis unde omnis iste natus error sit voluptatem accusantium doloremque latium, totam rem aperiam</p></div>
</article>
<article class="abs post" style="left:775px;top:2178px">
  <div class="post-img" role="img" aria-label="Hexagon network graphic glowing orange on a dark background" style="background:radial-gradient(circle at 50% 55%,#e0603a,#4a2a2a 55%,#1a1a1f)"></div>
  <div class="post-body"><div class="post-date">▦ October 17, 2018</div><h4>Quis autem vel eum iure reprehen derit qui in ea voluptate</h4><p>Sed ut perspiciatis unde omnis iste natus error sit voluptatem accusantium doloremque latium, totam rem aperiam</p></div>
</article>

<svg class="abs clouds" width="1200" height="140" viewBox="0 0 1200 140" aria-hidden="true">
  <path d="M0 80 Q60 30 130 60 Q190 20 260 55 Q330 15 410 50 Q480 25 550 55 Q620 20 700 50 Q770 15 850 52 Q920 25 990 55 Q1060 20 1130 50 Q1170 35 1200 45 V140 H0Z" fill="#fff"/>
</svg>

<div class="abs foot" style="left:130px;top:2815px">
  <h5>SIGN UP FOR NEWSLETTER</h5>
  <p class="foot-text">Excepteur sint occaecat cupidatat non proident, sunt in culpa qui officia deserunt</p>
  <div class="email-field">Enter email</div>
  <span class="sub-btn">SIGN UP</span>
</div>
<div class="abs foot" style="left:467px;top:2815px">
  <h5>CONTACT US</h5>
  <ul class="contact-list">
    <li><span style="color:var(--red)">●</span><span>Vextor<br>Linden Row, Harwick 4410-2290</span></li>
    <li><span style="color:var(--red)">✆</span><span>Phone: (555) 210-4388</span></li>
    <li><span style="color:var(--red)">✉</span><span>Email: info@vextor.com</span></li>
  </ul>
</div>
<div class="abs foot" style="left:770px;top:2815px">
  <h5>QUICK LINKS</h5>
  <ul class="links"><li>Home</li><li>About</li><li>Services</li><li>Blog</li><li>Pricing</li><li>Contact Us</li></ul>
</div>
<div class="abs foot" style="left:970px;top:2815px">
  <h5>SOCIAL</h5>
  <ul class="social"><li><span></span>Pagefront</li><li><span></span>Chirper</li><li><span></span>Orbit+</li><li><span></span>Reelhub</li></ul>
</div>

<div class="abs foot-rule"></div>
<p class="abs copyright">© Copyright 2018 Vextor. All Rights Reserved.</p>

</body>
</html>
```